NZ First of it's kind solutions directory and marketplace for busy Mums needs a business card design

We need a business card design for our new nationwide business in NZ (long term plans to go global). We provide solutions to the everyday challenges that busy Mums face by connecting them with quality communities and suppliers of carefully selected, relevant products and services. We sell direct via our online marketplace. The final design should communicate our values of inclusivity, quality and smart solutions. Colours should incorporate our logo colour palette of #477077 and #6ba8b2. Our website is at https://www.brightnestmums.example

Target Market(s)

busy Mums, Age 28 – 50, female, income over $100K, location main centres NZ primarily but NZ wide. Is likely juggling work or career with a young family. Probably had hobbies which have fallen by the wayside.
-Wants to succeed in her chosen career without compromising on family life
-to successfully juggle her career without feeling like she is compromising her children
- Is time poor, something always has to give and it’s generally her health (she’ll stay up late, get stressed)
- probably ex corporate or professional career. Has discretional income

Industry/Entity Type

Business

Contact Information for Business Card

Lena Forbisher, Founder, BrightNestMums.example (Strapline Tap; Gather; Sorted), 47 Kowhai Terrace, Ellerslie, Auckland 1051, New Zealand. Mob: 021 483 517 Ph: +64 (0)9 571 4860

Font styles to use
Other font styles liked:
• Raleway, and/or Architects Daughter

Colors
00a990
33b8a4
86cfc6
cfeae6

Requirements
Must have
• the above details, streamline. the logo and colours associated with those logos
Should not have
• foil or metallic colours

```html
<!DOCTYPE html>
<html lang="en">
<head>
<meta charset="utf-8">
<title>BrightNestMums – Business Card</title>
<link rel="stylesheet" href="https://fonts.googleapis.com/css2?family=Roboto:ital,wght@0,400;0,500;0,700;1,400&display=swap">
<style>
  :root {
    --teal-dark: #477077;
    --teal-light: #6ba8b2;
    --ink: #3a3f42;
    --card: #f7f7f6;
    --backdrop: #e4e4e4;
  }
  * { margin: 0; padding: 0; box-sizing: border-box; }
  html, body { width: 1200px; height: 576px; overflow: hidden; }
  body {
    background: var(--backdrop);
    font-family: "Roboto", Arial, sans-serif;
    color: var(--ink);
    position: relative;
  }
  .card {
    position: absolute;
    top: 138px;
    width: 484px;
    height: 293px;
    background: var(--card);
    border-radius: 14px;
    overflow: hidden;
  }
  .card--front { left: 82px; }
  .card--back { left: 602px; }

  /* front */
  .front-disc {
    position: absolute;
    left: 13px;
    top: 120px;
    width: 170px;
    height: 170px;
    border-radius: 50%;
    background: var(--teal-dark);
  }
  .front-brand {
    position: absolute;
    left: 218px;
    top: 196px;
    font-size: 30px;
    font-weight: 500;
    letter-spacing: -0.3px;
    color: var(--teal-dark);
  }
  .strapline {
    position: absolute;
    left: 220px;
    top: 238px;
    font-size: 10.5px;
    letter-spacing: 3.2px;
    text-transform: uppercase;
    color: var(--ink);
  }
  .strapline .bar { color: var(--teal-light); margin: 0 4px; }

  /* back */
  .wave { position: absolute; left: 0; top: 0; width: 484px; height: 150px; }
  .holder {
    position: absolute;
    right: 20px;
    top: 28px;
    text-align: right;
    color: #fff;
  }
  .holder__name { font-size: 19px; font-weight: 700; }
  .holder__role { font-size: 11px; font-style: italic; margin-top: 2px; }
  .back-brand {
    position: absolute;
    left: 30px;
    top: 108px;
    display: flex;
    align-items: center;
    gap: 12px;
    font-size: 31px;
    font-weight: 500;
    letter-spacing: -0.3px;
    color: var(--teal-dark);
  }
  .back-brand__dot {
    width: 24px; height: 24px;
    border-radius: 50%;
    background: var(--teal-dark);
  }
  .contacts {
    position: absolute;
    left: 32px;
    top: 192px;
    list-style: none;
    font-size: 11.5px;
    line-height: 18px;
  }
  .contacts li { display: flex; align-items: center; gap: 8px; }
  .contacts svg { width: 10px; height: 10px; fill: var(--teal-dark); flex: none; }
  .address {
    position: absolute;
    right: 31px;
    top: 228px;
    text-align: right;
    font-size: 11.5px;
    line-height: 19px;
  }
</style>
</head>
<body>

<section class="card card--front">
  <div class="front-disc" aria-hidden="true"></div>
  <div class="front-brand">BrightNestMums</div>
  <div class="strapline">Tap<span class="bar">|</span>Gather<span class="bar">|</span>Sorted</div>
</section>

<section class="card card--back">
  <svg class="wave" viewBox="0 0 484 150" preserveAspectRatio="none" aria-hidden="true">
    <path fill="var(--teal-dark)" d="M0,0 H484 V122 C420,114 350,86 270,48 C200,18 110,6 0,16 Z"/>
    <path fill="var(--teal-light)" d="M0,38 C110,18 210,24 290,58 C370,94 430,128 484,136 V127 C430,120 370,88 296,50 C215,10 110,6 0,28 Z"/>
  </svg>
  <div class="holder">
    <div class="holder__name">Lena Forbisher</div>
    <div class="holder__role">Founder</div>
  </div>
  <div class="back-brand"><span class="back-brand__dot" aria-hidden="true"></span>BrightNestMums</div>

  <ul class="contacts">
    <li><svg viewBox="0 0 10 10" aria-hidden="true"><rect x="2.5" y="0.5" width="5" height="9" rx="1"/></svg>021 483 517</li>
    <li><svg viewBox="0 0 10 10" aria-hidden="true"><path d="M1,3 C1,1 9,1 9,3 V4 H7 V3 H3 V4 H1 Z M2,5 H8 L9,9 H1 Z"/></svg>+64 (0)9 571 4860</li>
    <li><svg viewBox="0 0 10 10" aria-hidden="true"><path d="M0.5,2 H9.5 V8 H0.5 Z M1,2.5 L5,5.5 L9,2.5" stroke="#fff" stroke-width="0.6"/></svg>www.BrightNestMums.example</li>
    <li><svg viewBox="0 0 10 10" aria-hidden="true"><circle cx="5" cy="5" r="4.5"/><path d="M0.5,5 H9.5 M5,0.5 C2.5,3 2.5,7 5,9.5 M5,0.5 C7.5,3 7.5,7 5,9.5" stroke="#fff" stroke-width="0.6" fill="none"/></svg>lena@brightnestmums.example</li>
  </ul>

  <div class="address">47 Kowhai Terrace, Ellerslie,<br>Auckland 1051, New Zealand</div>
</section>

</body>
</html>
```